Seeking a new website design for electrical contracting company

Brisket & Vane electrical contracting needs a new website for brisket-vane.example

We are looking for modern and something real cool with motion for a landing page. we have some cool images from our photo shoot. maybe even 3d motion our existing logo. we would like something we can edit with news and events and update a past project page. Also allow to take payment
stock images at
https://lorapellwinphotos.picvault-demo.example/Brisket-and-Vane

Target Market(s)

construction , home owners , business owners,

Industry/Entity Type

construction , electrical

Coding

Number of Pages Required

5+ page

Font styles to use
Serif
Sans Serif

Colors
0054AA
0677BA
7BADD7
CADEEF
E8F1F8
0094D4
00A9DD
6FCCEA
C7EBF8
E9F6FB
FFF300
FFF600
FEFA6F
FFFEC7
FFFEE8

Requirements
Must have
• excitement, motion, selling professionalism,

```html
<!DOCTYPE html>
<html lang="en">
<head>
<meta charset="utf-8">
<title>Brisket &amp; Vane Electrical Contractors</title>
<link rel="stylesheet" href="https://fonts.googleapis.com/css2?family=Outfit:wght@500;600;700&family=Lato:wght@400;700&display=swap">
<style>
:root{
  --night:#080c26;
  --navy:#252c6c;
  --ink:#1f2768;
  --orange:#f08a1d;
  --orange-deep:#dc7a17;
  --white:#ffffff;
  --text:#3a3a44;
  --muted:#cfd3ee;
  --footer:#0b0f29;
}
*{box-sizing:border-box;margin:0;padding:0}
html,body{width:1200px;height:4542px;overflow:hidden}
body{font-family:"Lato",sans-serif;color:var(--text);background:var(--white)}
section,header,footer{position:relative;width:1200px;overflow:hidden}
.abs{position:absolute}
.eyebrow{font-family:"Lato",sans-serif;color:var(--orange);font-size:22px}
.heading{font-family:"Outfit",sans-serif;font-weight:700;text-transform:uppercase;font-size:31px;line-height:40px;color:var(--ink)}
.btn{position:absolute;display:flex;align-items:center;justify-content:center;background:var(--orange);color:var(--white);font-weight:700;font-size:15px;border-radius:2px}
.photo{position:absolute;border-radius:2px}

/* hero */
.hero{height:645px;background:radial-gradient(ellipse at 78% 40%,#1d2f7a 0%,#0e1546 35%,var(--night) 70%)}
.hero-glow{position:absolute;left:640px;top:150px;width:560px;height:260px;border-radius:50%;background:radial-gradient(ellipse,rgba(150,140,255,.28),rgba(150,140,255,0) 70%)}
.brand{left:112px;top:34px;display:flex;align-items:center;gap:12px}
.brand-mark{width:66px;height:66px;border:5px solid var(--white);border-radius:6px}
.brand-name{font-family:"Outfit",sans-serif;font-weight:700;font-size:33px;color:var(--white);line-height:34px}
.brand-tag{font-family:"Outfit",sans-serif;font-size:11.5px;letter-spacing:2.2px;color:var(--white);margin-top:2px;margin-left:30px}
.nav{left:515px;top:38px;display:flex;align-items:center;font-size:14.5px;color:var(--white)}
.nav a{color:var(--white);text-decoration:none;margin-right:37px}
.nav .current{background:var(--orange);padding:7px 10px;border-radius:2px;margin-right:28px}
.hero-title{left:112px;top:178px;font-family:"Outfit",sans-serif;font-weight:700;font-size:51px;line-height:69px;color:var(--white);text-transform:uppercase}
.hero-title span{color:var(--orange)}
.hero-copy{left:112px;top:398px;width:440px;font-size:19px;line-height:32px;color:var(--white)}

/* services */
.services{height:578px;background:var(--navy)}
.services .heading{color:var(--white)}
.service-intro{left:680px;top:78px;width:410px;font-size:18.5px;line-height:30px;color:var(--white)}
.card{position:absolute;top:259px;width:225px;height:234px;background:var(--orange);border-radius:2px;text-align:center;color:var(--white)}
.card svg{margin-top:30px}
.card h3{font-family:"Outfit",sans-serif;font-weight:500;font-size:17px;line-height:27px;margin-top:12px}
.card .more{font-family:"Outfit",sans-serif;font-weight:500;font-size:17px;margin-top:13px}
.card.light{background:var(--white);color:var(--ink)}
.card.light .more{color:var(--orange)}

/* about */
.about{height:574px}
.about-copy{left:644px;width:430px;font-size:14.5px;line-height:24px;color:var(--text)}

/* projects */
.projects{height:746px}
.center{left:0;width:1200px;text-align:center}
.project{position:absolute;top:203px;width:308px;text-align:center}
.project .photo{position:static;height:252px;display:block}
.project h3{font-family:"Outfit",sans-serif;font-weight:500;font-size:21px;color:var(--ink);margin-top:20px}
.project p{font-size:14.5px;line-height:24px;margin:10px auto 0;width:270px}
.project .btn{position:relative;margin:23px auto 0;width:128px;height:37px}

/* cta */
.cta{height:371px;background:linear-gradient(100deg,#d8761a,#e8891f 45%,#de7b18)}
.beam{position:absolute;background:linear-gradient(180deg,rgba(255,255,255,.85),rgba(255,255,255,.1));transform-origin:top}

/* news */
.news{height:622px}

/* testimonials */
.testimonials{height:575px;background:var(--navy);color:var(--white)}
.review{position:absolute;top:236px;width:317px;height:228px;background:var(--orange);border-radius:3px;padding:32px 23px;color:var(--white)}
.review .stars{font-size:15px;letter-spacing:1px}
.review p{font-size:14.5px;line-height:22px;margin-top:20px}
.review h4{font-family:"Outfit",sans-serif;font-weight:500;font-size:17px;margin-top:18px}
.review time{font-size:12px;display:block;margin-top:6px}
.review.light{background:var(--white);color:var(--text)}
.review.light .stars,.review.light h4{color:var(--orange)}
.review.light h4{color:var(--ink)}

/* footer */
.footer{height:431px;background:var(--footer);color:var(--white)}
.footer h4{position:absolute;top:70px;font-family:"Outfit",sans-serif;font-weight:600;font-size:21px}
.footer ul{position:absolute;top:122px;list-style:none;font-size:14.5px;line-height:38.5px}
.contact-row{position:absolute;left:463px;display:flex;gap:20px;font-size:14.5px;line-height:24px}
.social{position:absolute;left:112px;top:270px;display:flex;gap:14px}
.social span{width:30px;height:30px;border-radius:4px;background:var(--white);display:block}
.social span.on{background:var(--orange)}
</style>
</head>
<body>

<header class="hero">
  <div class="hero-glow"></div>
  <svg class="abs" style="left:620px;top:0" width="80" height="260" viewBox="0 0 80 260"><polygon points="70,0 80,0 4,260 0,260" fill="rgba(255,255,255,.55)"/></svg>
  <div class="abs brand">
    <div class="brand-mark"></div>
    <div>
      <div class="brand-name">BRISKET &amp; VANE</div>
      <div class="brand-tag">ELECTRICAL CONTRACTORS</div>
    </div>
  </div>
  <nav class="abs nav">
    <a class="current">Home</a><a>About Us</a><a>Services</a><a>Projects</a><a>News &amp; Events</a><a style="margin-right:0">Contact</a>
  </nav>
  <h1 class="abs hero-title">Bringing <span>Power</span><br><span>and Precision</span><br>to Every Project</h1>
  <p class="abs hero-copy">High-performance electrical contracting for commercial, industrial, and mission-critical projects.</p>
  <div class="btn" style="left:112px;top:523px;width:164px;height:39px">Request a Quote</div>
</header>

<section class="services">
  <div class="abs eyebrow" style="left:112px;top:80px">Our Services</div>
  <h2 class="abs heading" style="left:112px;top:126px;color:#fff">Scalable Power Solutions<br>Seamless Execution</h2>
  <p class="abs service-intro">From design to installation, we deliver reliable, code-compliant electrical systems built for performance. We handle complex electrical builds with expert planning, reliable installation, and long-term support.</p>

  <div class="card" style="left:112px">
    <svg width="66" height="66" viewBox="0 0 66 66" fill="none" stroke="#fff" stroke-width="2"><circle cx="33" cy="33" r="30"/><path d="M26 14v10M40 14v10M22 24h22v10a11 11 0 0 1-22 0zM33 45v10"/></svg>
    <h3>Commercial Electrical<br>Contracting</h3><div class="more">Read More</div>
  </div>
  <div class="card light" style="left:363px">
    <svg width="66" height="66" viewBox="0 0 66 66" fill="none" stroke="#f08a1d" stroke-width="2"><circle cx="33" cy="33" r="30"/><path d="M33 14a13 13 0 0 0-7 24v6h14v-6a13 13 0 0 0-7-24zM27 49h12M35 20l-5 9h6l-5 9"/></svg>
    <h3>Industrial Electrical<br>Solutions</h3><div class="more">Read More</div>
  </div>
  <div class="card" style="left:614px">
    <svg width="66" height="66" viewBox="0 0 66 66" fill="none" stroke="#fff" stroke-width="2"><path d="M37 10 24 36h12l-6 22 16-28H34l6-20zM12 33h6M48 33h6M16 16l5 5M50 16l-5 5M16 50l5-5M50 50l-5-5"/></svg>
    <h3>Emergency Power &amp;<br>Generators</h3><div class="more">Read More</div>
  </div>
  <div class="card" style="left:865px">
    <svg width="66" height="66" viewBox="0 0 66 66" fill="none" stroke="#fff" stroke-width="2"><rect x="10" y="8" width="46" height="40" rx="2"/><rect x="16" y="14" width="34" height="28"/><path d="M35 18l-6 10h7l-5 10M18 48v8M48 48v8M14 56h38"/></svg>
    <h3>Power Distribution &amp;<br>Panel Upgrades</h3><div class="more">Read More</div>
  </div>
</section>

<section class="about">
  <div class="photo" role="img" aria-label="Electrician in high-visibility gear on a ladder servicing a ceiling unit" style="left:112px;top:86px;width:453px;height:436px;background:linear-gradient(150deg,#c9cbc8,#8f9593 50%,#e06a2a 80%,#b9b23a)"></div>
  <div class="abs eyebrow" style="left:644px;top:86px">About Us</div>
  <h2 class="abs heading" style="left:644px;top:128px">Powering Projects<br>Building Trust</h2>
  <p class="abs about-copy" style="top:235px">Brisket &amp; Vane is a full-service electrical contracting company delivering high-performance solutions across commercial, industrial, and mission-critical sectors.</p>
  <p class="abs about-copy" style="top:331px">From initial planning through final inspection, we bring technical precision, skilled craftsmanship, and decades of field-tested experience to every project. Whether you're building new, upgrading infrastructure, or maintaining complex systems — we wire with purpose, integrity, and pride.</p>
  <div class="btn" style="left:644px;top:483px;width:128px;height:37px">Read More</div>
</section>

<section class="projects">
  <div class="abs eyebrow center" style="top:6px">Past Projects</div>
  <h2 class="abs heading center" style="top:46px">Projects That Speak for Themselves</h2>
  <p class="abs center" style="top:96px;font-size:14.5px;line-height:24px">Built for performance. Trusted for precision. We bring deep expertise, clean execution,<br>and serious attention to detail — powering commercial and industrial<br>projects that can't afford to fail.</p>

  <div class="project" style="left:112px">
    <div class="photo" role="img" aria-label="Worker inspecting high-voltage substation equipment" style="background:linear-gradient(170deg,#c7d2d9,#8ea0ab 55%,#4b5660)"></div>
    <h3>Commercial Projects</h3>
    <p>Lorem ipsum dolor sit amet, consectetur adipiscing elit, sed do eiusmod tempor incididunt ut labore et magna aliqua</p>
    <div class="btn">View All</div>
  </div>
  <div class="project" style="left:446px">
    <div class="photo" role="img" aria-label="Two engineers in hard hats reviewing a laptop at an industrial plant" style="background:linear-gradient(160deg,#8a929c,#a44a26 50%,#d6b24a)"></div>
    <h3>Industrial Projects</h3>
    <p>Lorem ipsum dolor sit amet, consectetur adipiscing elit, sed do eiusmod tempor incididunt ut labore et magna aliqua</p>
    <div class="btn">View All</div>
  </div>
  <div class="project" style="left:780px">
    <div class="photo" role="img" aria-label="Electricians in yellow vests testing wiring on a panel" style="background:linear-gradient(160deg,#c2c8c6,#b9c94a 55%,#6f7e57)"></div>
    <h3>Specialized Projects</h3>
    <p>Lorem ipsum dolor sit amet, consectetur adipiscing elit, sed do eiusmod tempor incididunt ut labore et magna aliqua</p>
    <div class="btn">View All</div>
  </div>
</section>

<section class="cta">
  <svg class="abs" style="left:30px;top:0" width="110" height="200" viewBox="0 0 110 200"><polygon points="0,0 18,0 110,200 96,200" fill="rgba(255,255,255,.7)"/></svg>
  <svg class="abs" style="left:990px;top:200px" width="200" height="171" viewBox="0 0 200 171"><polygon points="0,0 14,0 200,171 160,171" fill="rgba(255,255,255,.75)"/></svg>
  <div class="abs center" style="top:70px;font-size:22px;color:var(--ink)">Ready to Power Up?</div>
  <h2 class="abs heading center" style="top:110px;color:#fff">Powering Your Future, Today</h2>
  <p class="abs center" style="top:162px;font-size:14.5px;line-height:24px;color:#fff">Expert electrical solutions for every project. Reliable, efficient, and built to last. Whether you're<br>planning a new build, upgrading systems, or need emergency electrical services, we're here<br>to bring your project to life. Let's get started today!</p>
  <div class="btn" style="left:513px;top:262px;width:173px;height:37px;background:var(--ink)">Start Your Project</div>
</section>

<section class="news">
  <div class="abs eyebrow" style="left:112px;top:118px">News &amp; Events</div>
  <h2 class="abs heading" style="left:112px;top:158px">Stay Updated With Our<br>Latest News &amp; Events</h2>
  <div class="abs" style="left:112px;top:249px;font-size:16.5px;line-height:22px;color:var(--ink);font-weight:700;width:360px">Event 1: Powering the Future — Industry Conference 2025</div>
  <p class="abs" style="left:112px;top:311px;width:400px;font-size:14.5px;line-height:22.5px">Whether it's a new project, an upcoming industry event, or important company news, you can find all the latest happenings here. Join us at this year's premier electrical industry event where we'll be showcasing our innovative solutions and sharing insights on the future of electrical contracting.</p>
  <div class="btn" style="left:112px;top:481px;width:128px;height:37px">View All</div>
  <div class="photo" role="img" aria-label="Overhead view of a team in harnesses and helmets gathered in a training hall" style="left:634px;top:86px;width:454px;height:453px;background:radial-gradient(circle at 50% 55%,#c9a44a,#7c8480 45%,#4a5250)"></div>
</section>

<section class="testimonials">
  <div class="abs center" style="top:79px;font-size:22px;color:#fff">Our Testimonials</div>
  <h2 class="abs heading center" style="top:120px;color:#fff">What Our Clients Are Saying</h2>
  <p class="abs center" style="top:164px;font-size:14.5px;line-height:24px;color:#fff">We take pride in building lasting relationships and delivering<br>exceptional electrical services.</p>

  <div class="review" style="left:112px">
    <div class="stars">★★★★★</div>
    <p>Excepteur sint occaecat cupidatat non proident, sunt in culpa qui officia deserunt mollit anim id est laborum.</p>
    <h4>Whitcombe</h4><time>Apr 18 2025</time>
  </div>
  <div class="review light" style="left:441px">
    <div class="stars">★★★★★</div>
    <p>Excepteur sint occaecat cupidatat non proident, sunt in culpa qui officia deserunt mollit anim id est laborum.</p>
    <h4>Marla</h4><time>Apr 18 2025</time>
  </div>
  <div class="review" style="left:771px">
    <div class="stars">★★★★★</div>
    <p>Excepteur sint occaecat cupidatat non proident, sunt in culpa qui officia deserunt mollit anim id est laborum.</p>
    <h4>Genevieve</h4><time>Apr 18 2025</time>
  </div>
  <div class="abs" style="left:569px;top:486px;display:flex;gap:5px">
    <span style="width:18px;height:6px;background:var(--orange);display:block"></span>
    <span style="width:18px;height:6px;background:#fff;display:block"></span>
    <span style="width:18px;height:6px;background:#fff;display:block"></span>
  </div>
</section>

<footer class="footer">
  <h4 style="left:113px">About Us</h4>
  <p class="abs" style="left:112px;top:120px;width:280px;font-size:14.5px;line-height:24px">Whether you're building new, upgrading infrastructure, or maintaining complex systems — we wire with purpose, integrity, and pride.</p>
  <div class="social" aria-label="Social media links"><span class="on"></span><span></span><span></span><span></span></div>

  <h4 style="left:463px">Contact Us</h4>
  <div class="contact-row" style="top:122px">
    <svg width="18" height="22" viewBox="0 0 18 22" fill="none" stroke="#fff" stroke-width="1.6"><path d="M9 21s7-7 7-12A7 7 0 0 0 2 9c0 5 7 12 7 12z"/><circle cx="9" cy="9" r="2.5"/></svg>
    <div>48 Alder Row Dr.<br>Fernhollow NH 03999</div>
  </div>
  <div class="contact-row" style="top:210px">
    <svg width="18" height="18" viewBox="0 0 18 18" fill="none" stroke="#fff" stroke-width="1.6"><path d="M4 1l3 4-2 2a10 10 0 0 0 6 6l2-2 4 3-2 3C8 17 1 10 1 3z"/></svg>
    <div>1-555-010-4477</div>
  </div>
  <div class="contact-row" style="top:272px">
    <svg width="18" height="18" viewBox="0 0 18 18" fill="none" stroke="#fff" stroke-width="1.6"><rect x="1" y="3" width="16" height="12"/><path d="M1 3l8 7 8-7"/></svg>
    <div>jay@brisket-vane.example</div>
  </div>

  <h4 style="left:760px">Quick Links</h4>
  <ul style="left:760px"><li>Home</li><li>About Us</li><li>Services</li><li>Projects</li><li>News &amp; Events</li></ul>

  <h4 style="left:977px">Other Links</h4>
  <ul style="left:977px"><li>FAQs</li><li>Support</li><li>Contact Us</li><li>Privacy Policy</li><li>Terms of Service</li></ul>

  <div class="abs center" style="top:396px;font-size:12.5px">Copyright © 2025 Brisket &amp; Vane electrical contracting. All rights reserved.</div>
</footer>

</body>
</html>
```